Simple Business Card Design for Tavlo

Job:

Make a very simple, minimalist business card design with my details including adjusted logo. One side to be white (with logo & text). Other side to be yellow - try plain or with logo (or part of logo eg Z). Need business card to have continuity with website.

Logo:
Our logo is made from a free download font website:
http://www.typewell.net/search.php?q=rubber
but the spacing/kerning needs correcting/adjusting as the font spaces unevenly between letters (see attached files). Need logo to be very crisp/sharp when printed.

Printing:
We will be using Plika.com so the design needs to conform to their requirements, see here:

http://uk.plika.com/products/luxe/business-cards.html (scroll down for dimensions and guidelines)

Design:

must say "plant-based food consulting" underneath logo or somewhere
no address needed in contact section
sharp corners (not rounded)
one side white, one side yellow

name: Rosalind Whitcombe
1xmobile number: +44 7700900463
1xtwiiter: @brimcounsel
website address www.orchardtable.com
email address brim@orchardtable.com

Should be easy quick job, prompt + detailed feedback given, am online in UK 9am-10pm for next 3 days. Website is www.orchardtable.com

Industry/Entity Type

Business

Requirements
Must have
• The logo must be corrected. The kerning is not right.

Please use a warm-grey for text

Please submit in matt format, we will be printing matt finish.

Should not have
• Avoid using banners or curvy highlights

Please avoid using black

Please avoid submitting in gloss finish

```html
<!DOCTYPE html>
<html lang="en">
<head>
<meta charset="utf-8">
<title>BRIM Business Card</title>
<link href="https://fonts.googleapis.com/css2?family=Cinzel:wght@400;700&display=swap" rel="stylesheet">
<style>
  :root {
    --backdrop: #e3e3e3;
    --paper-white: #fbfaf7;
    --paper-yellow: #efe05a;
    --warm-grey: #6e6862;
    --warm-grey-dark: #57524c;
    --warm-grey-light: #a39d95;
    --rule: #cfc9c1;
  }
  * { margin: 0; padding: 0; box-sizing: border-box; }
  html, body {
    width: 1200px;
    height: 720px;
    overflow: hidden;
    background: var(--backdrop);
    font-family: "Cinzel", serif;
  }
  .stage {
    position: relative;
    width: 1200px;
    height: 720px;
  }
  .card {
    position: absolute;
    top: 242px;
    width: 420px;
    height: 238px;
    overflow: hidden;
  }
  .card--front { left: 147px; background: var(--paper-white); }
  .card--back { left: 633px; background: var(--paper-yellow); }

  .brand {
    position: absolute;
    font-family: "Cinzel", serif;
    font-weight: 700;
    color: var(--warm-grey-dark);
    line-height: 1;
    letter-spacing: 2px;
  }
  .card--front .brand {
    left: 22px;
    top: 26px;
    font-size: 60px;
  }
  .card--back .brand {
    left: 0;
    right: 0;
    top: 74px;
    text-align: center;
    font-size: 86px;
  }

  .tagline {
    position: absolute;
    font-family: "Cinzel", serif;
    font-weight: 400;
    color: var(--warm-grey);
    letter-spacing: 1px;
    line-height: 1;
  }
  .card--front .tagline {
    left: 24px;
    top: 92px;
    font-size: 9px;
  }
  .card--back .tagline {
    left: 0;
    right: 0;
    top: 170px;
    text-align: center;
    font-size: 11px;
    letter-spacing: 2px;
  }

  .identity {
    position: absolute;
    right: 20px;
    top: 97px;
    text-align: right;
  }
  .identity__name {
    font-weight: 700;
    font-size: 12px;
    color: var(--warm-grey-dark);
    letter-spacing: 0.3px;
  }
  .identity__role {
    font-size: 9.5px;
    color: var(--warm-grey);
    margin-top: 1px;
  }

  .divider {
    position: absolute;
    left: 21px;
    top: 134px;
    width: 379px;
    height: 1px;
    background: var(--rule);
  }

  .contacts {
    position: absolute;
    left: 21px;
    top: 148px;
    list-style: none;
  }
  .contacts__item {
    display: flex;
    align-items: center;
    height: 12.3px;
    font-size: 8.6px;
    color: var(--warm-grey);
  }
  .contacts__icon {
    width: 10px;
    height: 8px;
    margin-right: 8px;
    flex: none;
  }
</style>
</head>
<body>
<main class="stage">

  <section class="card card--front">
    <div class="brand">BRIM</div>
    <div class="tagline">plant-based food consulting</div>

    <div class="identity">
      <div class="identity__name">Rosalind Whitcombe</div>
      <div class="identity__role">Manager</div>
    </div>

    <div class="divider"></div>

    <ul class="contacts">
      <li class="contacts__item">
        <svg class="contacts__icon" viewBox="0 0 10 8" aria-hidden="true">
          <path fill="var(--warm-grey-light)" d="M0.5,2.5 C1,0.5 9,0.5 9.5,2.5 L7.5,3 L7,2 L3,2 L2.5,3 Z"/>
          <rect x="2.5" y="3.5" width="5" height="4" rx="0.6" fill="var(--warm-grey-light)"/>
        </svg>
        +44 7700 900463
      </li>
      <li class="contacts__item">
        <svg class="contacts__icon" viewBox="0 0 10 8" aria-hidden="true">
          <rect x="0.5" y="0.8" width="9" height="6.4" fill="var(--warm-grey-light)"/>
          <path d="M0.8,1.2 L5,4.6 L9.2,1.2 M0.8,6.8 L3.8,3.8 M9.2,6.8 L6.2,3.8" stroke="var(--paper-white)" stroke-width="0.8" fill="none"/>
        </svg>
        brim@orchardtable.com
      </li>
      <li class="contacts__item">
        <svg class="contacts__icon" viewBox="0 0 10 8" aria-hidden="true">
          <rect x="1" y="0.8" width="8" height="5" fill="none" stroke="var(--warm-grey-light)" stroke-width="1.2"/>
          <rect x="3.5" y="6.4" width="3" height="1.2" fill="var(--warm-grey-light)"/>
        </svg>
        www.orchardtable.com
      </li>
    </ul>
  </section>

  <section class="card card--back">
    <div class="brand">BRIM</div>
    <div class="tagline">plant-based food consulting</div>
  </section>

</main>
</body>
</html>
```